Postcard design to acquire new clients for my Property Management Company

I'm looking for a postcard design that I can send to prospective clients detailing information about my company and services.
Postcard should be eye catching and contain information from www.bramblecrestpm.com. I've provided a few screen shots for the most important information and my logo.
Target Market(s)
Real Estate
Industry/Entity Type
Real Estate
Font styles to use
Sans Serif
Requirements
Must have
- Must be eye catching!! this will be a direct mail piece - I'd like for the card to be read and not tossed in the trash immediately.
Design que from the logo.
A place to write / print the receipts name and address.
our physical address - 2387 Hollow Pine Road, Lubbock, TX 79852.
Should not have
- the contact information on the business card is not accurate - please use info from website.

```html
<!DOCTYPE html>
<html lang="en">
<head>
<meta charset="utf-8">
<title>Bramblecrest Property Management – Postcard</title>
<link rel="stylesheet" href="https://fonts.googleapis.com/css2?family=Montserrat:wght@400;500;600;700;800&family=Oswald:wght@400;500&family=Roboto+Condensed:wght@400;500&display=swap">
<style>
:root{
  --navy:#0d4a87;
  --band-blue:#0e4d8d;
  --charcoal:#3c3c3d;
  --panel:#f1f3f3;
  --white:#ffffff;
  --line:#a9b3bd;
  --stage:#cfcfcf;
}
*{box-sizing:border-box;margin:0;padding:0}
html,body{width:1200px;height:1200px;overflow:hidden;background:var(--stage)}
body{position:relative;font-family:"Montserrat",sans-serif}
.card{position:absolute;left:200px;width:800px;height:540px;overflow:hidden;background:var(--white)}
.card--front{top:40px}
.card--back{top:620px}
.abs{position:absolute}

/* FRONT */
.hero{left:0;top:0;width:800px;height:348px;
  background:
    linear-gradient(180deg,rgba(0,0,0,0) 55%,rgba(60,70,60,.35) 100%),
    radial-gradient(ellipse at 62% 62%,rgba(240,200,110,.55) 0%,rgba(240,200,110,0) 38%),
    linear-gradient(180deg,#5560b4 0%,#6a74c2 30%,#5a5e80 55%,#4b4c58 78%,#6d7f62 100%);}
.brand{left:44px;top:42px;color:var(--white);font-weight:600}
.brand__name{font-size:24px;letter-spacing:4px;line-height:1}
.brand__sub{font-size:11.5px;letter-spacing:3.6px;margin-top:6px;line-height:1}
.tagline{left:491px;top:42px;color:var(--white);font-size:15.5px;line-height:20px;letter-spacing:.2px}
.tagline b{font-weight:700;display:block}
.services-strip{left:0;top:288px;width:800px;height:60px;
  background:linear-gradient(90deg,rgba(255,255,255,.88) 0%,rgba(255,255,255,.8) 60%,rgba(255,255,255,0) 92%)}
.services-title{left:44px;top:295px;font-size:38px;font-weight:800;letter-spacing:3px;color:var(--navy);line-height:46px}
.band{left:0;top:356px;width:800px;height:184px}
.service{position:absolute;display:flex;align-items:center;color:var(--white);font-weight:600;font-size:14.5px;letter-spacing:.3px;white-space:nowrap}
.service__icon{width:29px;height:29px;border-radius:50%;background:var(--white);display:flex;align-items:center;justify-content:center;margin-right:11px;flex:none}
.service__icon svg{width:17px;height:17px}
.rule{position:absolute;height:1px;background:rgba(255,255,255,.7)}
.contact{position:absolute;display:flex;align-items:center;color:var(--white);white-space:nowrap}
.contact__icon{width:20px;height:20px;border-radius:50%;background:#8d8f92;display:flex;align-items:center;justify-content:center;flex:none}
.contact__icon svg{width:12px;height:12px}
.phone{font-family:"Oswald",sans-serif;font-weight:400;font-size:37px;letter-spacing:.3px;line-height:1}
.web{font-weight:700;font-size:21px;letter-spacing:0;line-height:1}
.small{font-family:"Roboto Condensed",sans-serif;font-size:12.5px;font-weight:500}

/* BACK */
.pricing-title{left:36px;top:30px;font-size:24.5px;font-weight:800;letter-spacing:2.4px;color:var(--navy);line-height:30px}
.tier{left:38px;height:124px}
.tier__bg{position:absolute;inset:0}
.tier__title{position:absolute;left:29px;top:17px;color:var(--white);font-weight:700;font-size:15px;letter-spacing:2px}
.tier__sub{position:absolute;left:30px;top:42px;color:var(--white);font-weight:600;font-size:7.5px;letter-spacing:4.6px}
.tier__rate{position:absolute;left:28px;top:56px;color:var(--white);font-weight:700;font-size:60px;line-height:60px;letter-spacing:-1px}
.tier__unit{position:absolute;color:var(--white);font-weight:700;font-size:7.5px;line-height:9.5px}
.tier__list{position:absolute;left:263px;top:11px;list-style:none}
.tier__list li{display:flex;align-items:center;color:var(--white);font-size:9.5px;line-height:13.2px;letter-spacing:.2px;white-space:nowrap}
.tier__list li svg{width:7px;height:7px;margin-right:6px;flex:none}
.stamp{left:636px;top:27px;width:84px;height:100px;border:1px solid #6e6e6e}
.addr-line{left:591px;width:173px;height:1.5px;background:#b7b7b7}
.brand--back{left:591px;top:423px;color:var(--navy)}
.brand--back .brand__name{font-size:19px;letter-spacing:3.2px}
.brand--back .brand__sub{font-size:9.5px;letter-spacing:2.5px;margin-top:4px}
.footer{left:0;top:473px;width:800px;height:67px}
</style>
</head>
<body>

<!-- FRONT OF POSTCARD -->
<section class="card card--front" aria-label="Postcard front">
  <div class="abs hero" role="img" aria-label="Photograph of a modern two-storey house at dusk with glowing windows and lit glass garage doors"></div>

  <div class="abs brand">
    <div class="brand__name">BRAMBLECREST</div>
    <div class="brand__sub">PROPERTY MANAGEMENT</div>
  </div>

  <p class="abs tagline">CHOOSE THE RIGHT PROPERTY<b>MANAGEMENT SYSTEM</b></p>

  <div class="abs services-strip"></div>
  <h2 class="abs services-title">OUR SERVICES</h2>

  <svg class="abs band" viewBox="0 0 800 184" aria-hidden="true">
    <defs>
      <linearGradient id="streak" x1="0" y1="0" x2="1" y2="0">
        <stop offset="0" stop-color="#ffffff" stop-opacity="0"/>
        <stop offset="1" stop-color="#ffffff" stop-opacity=".35"/>
      </linearGradient>
    </defs>
    <rect width="800" height="184" fill="var(--band-blue)"/>
    <polygon points="470,0 503,0 441,184 380,184" fill="url(#streak)"/>
    <polygon points="503,0 800,0 800,184 441,184" fill="var(--charcoal)"/>
  </svg>

  <!-- services list -->
  <div class="service" style="left:45px;top:375px">
    <span class="service__icon"><svg viewBox="0 0 20 20"><path d="M10 2 1 10h3v8h5v-5h2v5h5v-8h3z" fill="var(--navy)"/></svg></span>Property Marketing</div>
  <div class="rule" style="left:85px;top:404px;width:137px"></div>
  <div class="service" style="left:45px;top:408px">
    <span class="service__icon"><svg viewBox="0 0 20 20" fill="var(--navy)"><circle cx="7" cy="6" r="3.2"/><circle cx="14" cy="6.5" r="2.6"/><path d="M1 17c0-4 2.7-6 6-6s6 2 6 6z"/><path d="M13 11c3 0 6 1.6 6 5h-5c0-2-.4-3.6-1-5z"/></svg></span>Tenant Screening</div>
  <div class="rule" style="left:85px;top:437px;width:137px"></div>
  <div class="service" style="left:45px;top:441px">
    <span class="service__icon"><svg viewBox="0 0 20 20"><text x="10" y="16" text-anchor="middle" font-family="Montserrat,sans-serif" font-weight="800" font-size="16" fill="var(--navy)">$</text></svg></span>Rent Collection</div>
  <div class="rule" style="left:85px;top:469px;width:137px"></div>
  <div class="service" style="left:45px;top:475px">
    <span class="service__icon"><svg viewBox="0 0 20 20" fill="var(--navy)"><path d="M8 3h7l2 3-4 1-8 10-2-2 8-9-3-1z"/></svg></span>Maintenance</div>

  <div class="service" style="left:243px;top:375px">
    <span class="service__icon"><svg viewBox="0 0 20 20"><circle cx="8.5" cy="8.5" r="5" fill="none" stroke="var(--navy)" stroke-width="2.6"/><path d="M12 12l5 5" stroke="var(--navy)" stroke-width="3" stroke-linecap="round"/></svg></span>Property Inspections</div>
  <div class="rule" style="left:282px;top:404px;width:149px"></div>
  <div class="service" style="left:243px;top:408px">
    <span class="service__icon"><svg viewBox="0 0 20 20" fill="var(--navy)"><rect x="3" y="16" width="14" height="1.6"/><rect x="3" y="3" width="1.6" height="14"/><rect x="6" y="9" width="2" height="6"/><rect x="9.5" y="6" width="2" height="9"/><rect x="13" y="10" width="2" height="5"/></svg></span>Financial Reporting</div>
  <div class="rule" style="left:282px;top:437px;width:149px"></div>
  <div class="service" style="left:243px;top:441px">
    <span class="service__icon"><svg viewBox="0 0 20 20"><path d="M10 2 3 5v5c0 4 3 7 7 8 4-1 7-4 7-8V5z" fill="var(--navy)"/><path d="M10 5v10c2.3-.8 4-3 4-5V7z" fill="#fff"/></svg></span>Evictions</div>
  <div class="rule" style="left:282px;top:469px;width:149px"></div>
  <div class="service" style="left:243px;top:475px">
    <span class="service__icon"><svg viewBox="0 0 20 20" fill="none" stroke="var(--navy)" stroke-width="1.6"><path d="M10 3v13M5 17h10M3 6h14"/><path d="M5 6 2.5 12h5zM15 6l-2.5 6h5z"/></svg></span>Legal Guidance</div>

  <!-- contact block -->
  <div class="contact" style="left:501px;top:381px">
    <span class="contact__icon"><svg viewBox="0 0 20 20"><path d="M5 2l3 4-2 2c1 2.5 3 4.5 5.5 5.5l2-2 4 3-2 3C9 17 3 11 2 4z" fill="#fff"/></svg></span>
    <span class="phone" style="margin-left:10px">(806) 555-0147</span></div>
  <div class="contact" style="left:501px;top:424px">
    <span class="contact__icon"><svg viewBox="0 0 20 20" fill="none" stroke="#fff" stroke-width="1.5"><circle cx="10" cy="10" r="7.5"/><ellipse cx="10" cy="10" rx="3.2" ry="7.5"/><path d="M2.5 10h15M4 6h12M4 14h12"/></svg></span>
    <span class="web" style="margin-left:10px">bramblecrestpm.com</span></div>
  <div class="contact" style="left:501px;top:455px">
    <span class="contact__icon"><svg viewBox="0 0 20 20" fill="none" stroke="#fff" stroke-width="1.6"><path d="M10 18s-5-6-5-10a5 5 0 0 1 10 0c0 4-5 10-5 10z"/><circle cx="10" cy="8" r="1.8"/></svg></span>
    <span class="small" style="margin-left:10px">2387 Hollow Pine Road Lubbock, Texas 79852</span></div>
  <div class="contact" style="left:501px;top:483px">
    <span class="contact__icon"><svg viewBox="0 0 20 20" fill="none" stroke="#fff" stroke-width="1.6"><rect x="3" y="5" width="14" height="10"/><path d="M3 5l7 6 7-6"/></svg></span>
    <span class="small" style="margin-left:10px">info@bramblecrestpm.com</span></div>
</section>

<!-- BACK OF POSTCARD -->
<section class="card card--back" aria-label="Postcard back">
  <svg class="abs" style="left:0;top:0" width="800" height="540" viewBox="0 0 800 540" aria-hidden="true">
    <polygon points="0,0 554,0 489,473 0,473" fill="var(--panel)"/>
  </svg>

  <h2 class="abs pricing-title">OUR PRICING</h2>

  <!-- tier 1 -->
  <div class="abs tier" style="top:71px;width:508px;clip-path:polygon(0 0,100% 0,calc(100% - 17px) 100%,0 100%)">
    <div class="tier__bg" role="img" aria-label="Blue-tinted aerial photograph of a residential neighbourhood" style="background:linear-gradient(100deg,#12477e 0%,#1d5894 45%,#174d86 100%)"></div>
    <div class="tier__title">LEASE ONLY</div>
    <div class="tier__sub">YOU JUST NEED TENANTS</div>
    <div class="tier__rate">9%</div>
    <div class="tier__unit" style="left:137px;top:71px">OF ANNUAL<br>LEASE</div>
    <ul class="tier__list">
      <li><svg viewBox="0 0 10 10" fill="none" stroke="#fff"><circle cx="5" cy="5" r="4.3"/><path d="M3 5h4M5.3 3.2 7 5 5.3 6.8"/></svg>of annual lease</li>
      <li><svg viewBox="0 0 10 10" fill="none" stroke="#fff"><circle cx="5" cy="5" r="4.3"/><path d="M3 5h4M5.3 3.2 7 5 5.3 6.8"/></svg>Professional Photography</li>
      <li><svg viewBox="0 0 10 10" fill="none" stroke="#fff"><circle cx="5" cy="5" r="4.3"/><path d="M3 5h4M5.3 3.2 7 5 5.3 6.8"/></svg>Marketing &amp; Advertising</li>
      <li><svg viewBox="0 0 10 10" fill="none" stroke="#fff"><circle cx="5" cy="5" r="4.3"/><path d="M3 5h4M5.3 3.2 7 5 5.3 6.8"/></svg>Property Showings</li>
      <li><svg viewBox="0 0 10 10" fill="none" stroke="#fff"><circle cx="5" cy="5" r="4.3"/><path d="M3 5h4M5.3 3.2 7 5 5.3 6.8"/></svg>Tenant Screening &amp; Qualifications</li>
      <li><svg viewBox="0 0 10 10" fill="none" stroke="#fff"><circle cx="5" cy="5" r="4.3"/><path d="M3 5h4M5.3 3.2 7 5 5.3 6.8"/></svg>Lease Execution</li>
      <li><svg viewBox="0 0 10 10" fill="none" stroke="#fff"><circle cx="5" cy="5" r="4.3"/><path d="M3 5h4M5.3 3.2 7 5 5.3 6.8"/></svg>Move In Coordination</li>
    </ul>
  </div>

  <!-- tier 2 -->
  <div class="abs tier" style="top:202px;width:489px;clip-path:polygon(0 0,100% 0,calc(100% - 17px) 100%,0 100%)">
    <div class="tier__bg" role="img" aria-label="Greyscale photograph of a smiling couple in their new home" style="background:linear-gradient(90deg,#4f4f50 0%,#7a7a7a 30%,#9a9a9a 45%,#666 62%,#505051 100%)"></div>
    <div class="tier__title">FULL SERVICE</div>
    <div class="tier__sub">OUR MOST POPULAR</div>
    <div class="tier__rate">10%</div>
    <div class="tier__unit" style="left:171px;top:66px">OF MONTHLY<br>RENT</div>
    <ul class="tier__list">
      <li><svg viewBox="0 0 10 10" fill="none" stroke="#fff"><circle cx="5" cy="5" r="4.3"/><path d="M3 5h4M5.3 3.2 7 5 5.3 6.8"/></svg>Includes Leasing Service</li>
      <li><svg viewBox="0 0 10 10" fill="none" stroke="#fff"><circle cx="5" cy="5" r="4.3"/><path d="M3 5h4M5.3 3.2 7 5 5.3 6.8"/></svg>24/7 Emergency Response</li>
      <li><svg viewBox="0 0 10 10" fill="none" stroke="#fff"><circle cx="5" cy="5" r="4.3"/><path d="M3 5h4M5.3 3.2 7 5 5.3 6.8"/></svg>Move In &amp; Out Inspections</li>
      <li><svg viewBox="0 0 10 10" fill="none" stroke="#fff"><circle cx="5" cy="5" r="4.3"/><path d="M3 5h4M5.3 3.2 7 5 5.3 6.8"/></svg>Professional Lease Enforcement</li>
      <li><svg viewBox="0 0 10 10" fill="none" stroke="#fff"><circle cx="5" cy="5" r="4.3"/><path d="M3 5h4M5.3 3.2 7 5 5.3 6.8"/></svg>Schedule &amp; Oversee all Repairs</li>
      <li><svg viewBox="0 0 10 10" fill="none" stroke="#fff"><circle cx="5" cy="5" r="4.3"/><path d="M3 5h4M5.3 3.2 7 5 5.3 6.8"/></svg>Pay all Invoices</li>
      <li><svg viewBox="0 0 10 10" fill="none" stroke="#fff"><circle cx="5" cy="5" r="4.3"/><path d="M3 5h4M5.3 3.2 7 5 5.3 6.8"/></svg>Monthly &amp; Year End Statements</li>
      <li><svg viewBox="0 0 10 10" fill="none" stroke="#fff"><circle cx="5" cy="5" r="4.3"/><path d="M3 5h4M5.3 3.2 7 5 5.3 6.8"/></svg>Annual Market Rent Analysis</li>
    </ul>
  </div>

  <!-- tier 3 -->
  <div class="abs tier" style="top:333px;width:470px;clip-path:polygon(0 0,100% 0,calc(100% - 17px) 100%,0 100%)">
    <div class="tier__bg" role="img" aria-label="Blue-tinted photograph of a family standing in a bright living room" style="background:linear-gradient(90deg,#16497f 0%,#1f5590 40%,#2b6199 55%,#174c85 75%,#21588f 100%)"></div>
    <div class="tier__title">LEASE ONLY</div>
    <div class="tier__sub">YOU JUST NEED TENANTS</div>
    <div class="tier__rate">12%</div>
    <div class="tier__unit" style="left:167px;top:70px">OF MONTHLY<br>RENT</div>
    <ul class="tier__list">
      <li><svg viewBox="0 0 10 10" fill="none" stroke="#fff"><circle cx="5" cy="5" r="4.3"/><path d="M3 5h4M5.3 3.2 7 5 5.3 6.8"/></svg>of annual lease</li>
      <li><svg viewBox="0 0 10 10" fill="none" stroke="#fff"><circle cx="5" cy="5" r="4.3"/><path d="M3 5h4M5.3 3.2 7 5 5.3 6.8"/></svg>Professional Photography</li>
      <li><svg viewBox="0 0 10 10" fill="none" stroke="#fff"><circle cx="5" cy="5" r="4.3"/><path d="M3 5h4M5.3 3.2 7 5 5.3 6.8"/></svg>Marketing &amp; Advertising</li>
      <li><svg viewBox="0 0 10 10" fill="none" stroke="#fff"><circle cx="5" cy="5" r="4.3"/><path d="M3 5h4M5.3 3.2 7 5 5.3 6.8"/></svg>Property Showings</li>
      <li><svg viewBox="0 0 10 10" fill="none" stroke="#fff"><circle cx="5" cy="5" r="4.3"/><path d="M3 5h4M5.3 3.2 7 5 5.3 6.8"/></svg>Tenant Screening &amp; Qualifications</li>
      <li><svg viewBox="0 0 10 10" fill="none" stroke="#fff"><circle cx="5" cy="5" r="4.3"/><path d="M3 5h4M5.3 3.2 7 5 5.3 6.8"/></svg>Lease Execution</li>
      <li><svg viewBox="0 0 10 10" fill="none" stroke="#fff"><circle cx="5" cy="5" r="4.3"/><path d="M3 5h4M5.3 3.2 7 5 5.3 6.8"/></svg>Move In Coordination</li>
    </ul>
  </div>

  <!-- mailing area -->
  <div class="abs stamp"></div>
  <div class="abs addr-line" style="top:189px"></div>
  <div class="abs addr-line" style="top:229px"></div>
  <div class="abs addr-line" style="top:269px"></div>
  <div class="abs addr-line" style="top:308px"></div>
  <div class="abs addr-line" style="top:348px"></div>

  <div class="abs brand brand--back">
    <div class="brand__name">BRAMBLECREST</div>
    <div class="brand__sub">PROPERTY MANAGEMENT</div>
  </div>

  <!-- footer -->
  <svg class="abs footer" viewBox="0 0 800 67" aria-hidden="true">
    <polygon points="0,0 573,0 566,67 0,67" fill="var(--charcoal)"/>
    <polygon points="583,0 800,0 800,67 575,67" fill="var(--band-blue)"/>
  </svg>
  <div class="contact" style="left:38px;top:492px">
    <span class="contact__icon"><svg viewBox="0 0 20 20"><path d="M5 2l3 4-2 2c1 2.5 3 4.5 5.5 5.5l2-2 4 3-2 3C9 17 3 11 2 4z" fill="#fff"/></svg></span>
    <span class="phone" style="margin-left:12px;font-size:33px">(806) 555-0147</span></div>
  <div class="contact" style="left:290px;top:496px">
    <span class="contact__icon"><svg viewBox="0 0 20 20" fill="none" stroke="#fff" stroke-width="1.5"><circle cx="10" cy="10" r="7.5"/><ellipse cx="10" cy="10" rx="3.2" ry="7.5"/><path d="M2.5 10h15M4 6h12M4 14h12"/></svg></span>
    <span class="web" style="margin-left:11px;font-size:19px">bramblecrestpm.com</span></div>
  <div class="contact" style="left:604px;top:481px">
    <span class="contact__icon" style="width:14px;height:14px"><svg viewBox="0 0 20 20" fill="none" stroke="#fff" stroke-width="1.8"><path d="M10 18s-5-6-5-10a5 5 0 0 1 10 0c0 4-5 10-5 10z"/><circle cx="10" cy="8" r="1.8"/></svg></span>
    <span class="small" style="margin-left:8px;font-size:8.5px">2387 Hollow Pine Road Lubbock, Texas 79852</span></div>
  <div class="contact" style="left:604px;top:499px">
    <span class="contact__icon" style="width:14px;height:14px"><svg viewBox="0 0 20 20" fill="none" stroke="#fff" stroke-width="1.8"><rect x="3" y="5" width="14" height="10"/><path d="M3 5l7 6 7-6"/></svg></span>
    <span class="small" style="margin-left:8px;font-size:8.5px">info@bramblecrestpm.com</span></div>
</section>

</body>
</html>
```